ORV Web Design Project

I'm looking for a small, friendly,functional, information based website. If you go through the attachments, you would know the nature of the business.
Updates

Hi,

I have uploaded a picture of the CEO, Mr. Delvan Kroth PLMAT member. Please feel free to use it whereever appropriate.

Thanks!

Hello, I have uploaded some references. I like the colours used on the bar and would w

Example of a we page . I like this layout for the inside pages.

I am changing the tabs on my website to:

Home
About us
Services
Contact us

The services tab will have three sub pages:

Immigration
Education
AccommodationAccommodation

Target Market(s)

Young international students willing to come to Canada to study, young international students willing to immigrate to Canada, parents of the students

Industry/Entity Type

Business

Requirements
Must have
• ORV HOME
ABOUT US
CONTACT
SERVICES
TAG LINE

The website should look n feel trendy, smart, current, factual, trustworthy etc....
Nice to have
• I am looking for a bold, attractive, eye catchy home page with less text! Something that makes a statement....
Should not have
• No Clip art, flash animation, no bells n whistles please

```html
<!DOCTYPE html>
<html lang="en">
<head>
<meta charset="utf-8">
<title>ORV Mission</title>
<link rel="stylesheet" href="https://fonts.googleapis.com/css2?family=Fredoka:wght@600&family=Open+Sans:wght@400;600&display=swap">
<style>
  :root {
    --bg-top: #6a0008;
    --bg-bottom: #a60214;
    --card: #ffffff;
    --band: #f0f0f0;
    --ink: #1e1e1e;
    --brand-red: #e0101e;
    --nav-grey: #7a7a7a;
    --nav-active: #f7941d;
    --slate: #48525c;
    --body-text: #2a2a2a;
    --footer-text: #f3d6d8;
    --photo-a: #e9dcd2;
    --photo-b: #d9c4b8;
  }
  * { box-sizing: border-box; margin: 0; padding: 0; }
  html, body { width: 1200px; height: 974px; overflow: hidden; }
  body {
    background: linear-gradient(180deg, var(--bg-top) 0%, var(--bg-bottom) 45%, var(--bg-bottom) 100%);
    font-family: "Open Sans", sans-serif;
    position: relative;
  }
  .page-card {
    position: absolute; left: 96px; top: 49px;
    width: 1008px; height: 850px;
    background: var(--card); border-radius: 4px; overflow: hidden;
  }
  .site-header { position: relative; height: 203px; }
  .brand { position: absolute; left: 34px; top: 34px; }
  .brand-mark { display: flex; align-items: center; gap: 10px; }
  .brand-square { width: 26px; height: 26px; background: var(--brand-red); }
  .brand-name {
    font-family: "Open Sans", sans-serif; font-weight: 600;
    font-size: 56px; line-height: 1; color: var(--ink); letter-spacing: 1px;
  }
  .brand-sub {
    margin-top: 6px; font-size: 15px; color: #444; letter-spacing: .2px;
  }
  .tagline {
    position: absolute; right: 36px; top: 68px;
    font-family: "Fredoka", sans-serif; font-weight: 600;
    font-size: 39px; line-height: 1; color: var(--ink); letter-spacing: 1px;
  }
  .tagline .accent { color: var(--brand-red); }
  .main-nav {
    position: absolute; right: 36px; top: 122px;
    display: flex; gap: 26px; list-style: none;
  }
  .main-nav a {
    font-size: 17px; color: var(--nav-grey); text-decoration: none;
  }
  .main-nav a.is-active { color: var(--nav-active); }
  .mission-band {
    position: relative; height: 393px; background: var(--band);
  }
  .visa-gallery {
    position: absolute; left: 22px; top: 10px; width: 466px; height: 383px;
    background: linear-gradient(160deg, var(--photo-a), var(--photo-b));
  }
  .mission-copy { position: absolute; left: 516px; top: 121px; width: 461px; }
  .mission-title {
    font-size: 17px; font-weight: 400; color: var(--ink);
    letter-spacing: .5px; margin-bottom: 17px;
  }
  .mission-text {
    font-size: 11.6px; line-height: 19.3px; color: var(--body-text);
    text-align: justify;
  }
  .promo { position: absolute; left: 199px; top: 676px; display: flex; align-items: center; gap: 22px; }
  .promo-mark { display: flex; align-items: center; gap: 8px; }
  .promo-mark .brand-square { width: 18px; height: 18px; }
  .promo-mark .brand-name { font-size: 38px; }
  .promo-headline {
    font-size: 29px; font-weight: 400; color: var(--slate);
    letter-spacing: 1px; line-height: 1;
  }
  .promo-headline .accent { color: var(--brand-red); }
  .promo-sub { margin-top: 6px; font-size: 14px; color: var(--slate); }
  .site-footer {
    position: absolute; left: 0; top: 926px; width: 1200px;
    text-align: center; font-size: 11px; color: var(--footer-text);
  }
</style>
</head>
<body>
  <div class="page-card">
    <header class="site-header">
      <div class="brand">
        <div class="brand-mark">
          <span class="brand-name">ORV</span>
          <span class="brand-square"></span>
        </div>
        <div class="brand-sub">Orvane Business Group</div>
      </div>
      <div class="tagline">Taking You <span class="accent">Onwards</span></div>
      <ul class="main-nav">
        <li><a href="#">Home</a></li>
        <li><a href="#">About Us</a></li>
        <li><a href="#">Services</a></li>
        <li><a href="#">Contact</a></li>
        <li><a href="#" class="is-active">ORV Mission</a></li>
      </ul>
    </header>

    <section class="mission-band">
      <div class="visa-gallery" role="img" aria-label="Three overlapping Canadian student visa documents with applicant photos"></div>
      <div class="mission-copy">
        <h2 class="mission-title">ORV MISSION</h2>
        <p class="mission-text">At ORV we are committed to our customer centered philosophy. Our mission is to help our clients achieve their goals by providing them with world class customer service that is both reliable and competitively superior. We are driven by our core values: ethics, expertise and leadership. We believe that honesty paves the way for true success. We have been there. We know what it takes.</p>
      </div>
    </section>

    <div class="promo">
      <div class="promo-mark">
        <span class="brand-name">ORV</span>
        <span class="brand-square"></span>
      </div>
      <div>
        <div class="promo-headline">DARE TO DREAM <span class="accent">CANADIAN</span></div>
        <div class="promo-sub">Your best partner for immigration &amp; education solution in Canada.</div>
      </div>
    </div>
  </div>

  <footer class="site-footer">Copyright © 2013 OrvaneBusinessGroup. All Rights Reserved.</footer>
</body>
</html>
```